Velk Partners Building Business Cards

We need a business card that reflects our business as "Solar Experts" in San Diego. Browse our website www.velkpartners.example our License needs to be displayed as "CSLB# 3867140" our phone number is (619) 555-0187

Save thousands on your electric bills and increase the value of your home while helping to protect the environment. Our solar installation experts will help you design the system that's right for you, using only the highest quality equipment that will look great and give you ideal performance. Our goal is to make you energy independent, and get your electric bill to 0.

Paul Osterby
(619) 555-0187
paul@velkpartners.example

Target Market(s)

Home owners in san diego looking for solar

Industry/Entity Type

Solar Energy

Contact Information for Business Card

Paul Osterby
(619) 555-0187
paul@velkpartners.example

Font styles to use
Other font styles liked:
• Use our logo font

Requirements
Must have
• License needs to be displayed as "CSLB# 3867140" our phone number is (619) 555-0187
Nice to have
• Real images of rooftop home solar in san diego
Should not have
• our business address

```html
<!DOCTYPE html>
<html lang="en">
<head>
<meta charset="utf-8">
<title>Velk Partners Building – Business Cards</title>
<link href="https://fonts.googleapis.com/css2?family=Open+Sans:wght@400;600;800&display=swap" rel="stylesheet">
<style>
  :root {
    --navy: #1a3a73;
    --sun: #f5a800;
    --paper: #ffffff;
    --ink: #3a3a3a;
    --stage: #e6eaea;
    --faint-sun: #fbf1dc;
  }
  * { box-sizing: border-box; margin: 0; padding: 0; }
  html, body { width: 1200px; height: 812px; overflow: hidden; }
  body {
    background: var(--stage);
    font-family: "Open Sans", Arial, sans-serif;
    position: relative;
  }
  .card {
    position: absolute;
    width: 540px;
    height: 309px;
    top: 252px;
    overflow: hidden;
    box-shadow: 0 6px 18px rgba(0,0,0,0.12);
  }
  .card-back { left: 40px; background: var(--navy); }
  .card-front { left: 620px; background: var(--paper); }

  /* Back */
  .back-mark {
    position: absolute; left: 0; right: 0; top: 104px;
    display: flex; align-items: center; justify-content: center; gap: 12px;
  }
  .back-mark .dot { width: 34px; height: 34px; border-radius: 50%; background: var(--sun); }
  .back-mark .brand { color: var(--paper); font-weight: 800; font-size: 27px; letter-spacing: -0.3px; }
  .back-url {
    position: absolute; left: 0; right: 0; top: 218px; text-align: center;
    color: var(--paper); font-size: 12px; letter-spacing: 2.4px;
  }

  /* Front */
  .front-shape { position: absolute; inset: 0; }
  .holder { position: absolute; right: 26px; top: 22px; text-align: right; }
  .holder-name { color: var(--sun); font-weight: 800; font-size: 19px; line-height: 1.1; }
  .holder-role { color: var(--paper); font-size: 13px; }
  .front-brand {
    position: absolute; left: 112px; top: 122px;
    display: flex; align-items: center; gap: 8px;
  }
  .front-brand .dot { width: 20px; height: 20px; border-radius: 50%; background: var(--sun); }
  .front-brand .brand { color: var(--navy); font-weight: 800; font-size: 25px; letter-spacing: -0.4px; }
  .contact { position: absolute; left: 112px; top: 186px; color: var(--ink); font-size: 13px; line-height: 20px; }
  .contact li { list-style: none; display: flex; align-items: center; gap: 7px; }
  .contact .license { margin-bottom: 4px; }
  .contact svg { width: 12px; height: 12px; flex: none; }
</style>
</head>
<body>

<section class="card card-back" aria-label="Business card back">
  <div class="back-mark">
    <span class="dot"></span>
    <span class="brand">Velk Partners Building</span>
  </div>
  <p class="back-url">WWW.VELKPARTNERS.EXAMPLE</p>
</section>

<section class="card card-front" aria-label="Business card front">
  <svg class="front-shape" viewBox="0 0 540 309" aria-hidden="true">
    <circle cx="455" cy="150" r="62" fill="var(--faint-sun)"/>
    <polygon points="0,0 540,0 540,118 86,44 60,118 0,118" fill="var(--navy)"/>
    <polyline points="540,124 90,51 64,124" fill="none" stroke="var(--sun)" stroke-width="5"/>
    <rect x="0" y="124" width="60" height="0" fill="var(--paper)"/>
  </svg>

  <div class="holder">
    <p class="holder-name">Paul Osterby</p>
    <p class="holder-role">CEO/Founder</p>
  </div>

  <div class="front-brand">
    <span class="brand">Velk Partners Building</span>
    <span class="dot"></span>
  </div>

  <ul class="contact">
    <li class="license">CSLB# 3867140</li>
    <li>
      <svg viewBox="0 0 12 12" aria-hidden="true"><path d="M3 1 L5 3.5 L4 5 Q5 7 7 8 L8.5 7 L11 9 L9.5 11 Q4 10.5 1 3 Z" fill="var(--navy)"/></svg>
      (619) 555-0187
    </li>
    <li>
      <svg viewBox="0 0 12 12" aria-hidden="true"><rect x="1" y="2.5" width="10" height="7" rx="1" fill="var(--navy)"/><path d="M1.5 3 L6 6.5 L10.5 3" fill="none" stroke="#fff" stroke-width="1"/></svg>
      paul@velkpartners.example
    </li>
    <li>
      <svg viewBox="0 0 12 12" aria-hidden="true"><circle cx="6" cy="6" r="5.5" fill="var(--navy)"/><ellipse cx="6" cy="6" rx="2.2" ry="5" fill="none" stroke="#fff" stroke-width="0.8"/><line x1="1" y1="6" x2="11" y2="6" stroke="#fff" stroke-width="0.8"/></svg>
      www.velkpartners.example
    </li>
  </ul>
</section>

</body>
</html>
```